Corvel Capital LLC

Need Professional Business cards for New Investment Fund

Target Market(s)

High Quality investors

Industry/Entity Type

Financial

Contact Information for Business Card

Phone Number +1 555 284 6190
Name Lukas Varenko
Title Fund Manager
email lv@FundCorvel.com
Website www.FundCorvel.com

Colors

Designer to choose colors to be used in the design.

Requirements
Must have
• Must have our Logo and all of the above. Must be made so lettering and loge can be raised

```html
<!DOCTYPE html>
<html lang="en">
<head>
<meta charset="utf-8">
<title>Orvanthe – Business Card</title>
<link rel="stylesheet" href="https://fonts.googleapis.com/css2?family=Jost:wght@500;600&family=Raleway:wght@400;500&display=swap">
<style>
  :root {
    --stage: #1c1c1c;
    --forest: #434f42;
    --leaf: #57b947;
    --paper: #ffffff;
    --ink: #3a4639;
  }
  * { box-sizing: border-box; margin: 0; padding: 0; }
  html, body { width: 1200px; height: 900px; overflow: hidden; }
  body {
    background: var(--stage);
    position: relative;
    font-family: "Raleway", sans-serif;
  }
  .card {
    position: absolute;
    left: 250px;
    width: 700px;
    height: 400px;
    overflow: hidden;
  }
  .card--back { top: 40px; background: var(--forest); }
  .card--front { top: 460px; background: var(--paper); }

  .brand {
    position: absolute;
    display: flex;
    align-items: center;
    gap: 12px;
    font-family: "Jost", sans-serif;
    font-weight: 600;
    letter-spacing: 2px;
    white-space: nowrap;
  }
  .brand__mark { width: 22px; height: 22px; background: var(--leaf); flex: none; }
  .card--back .brand { left: 0; right: 0; top: 172px; justify-content: center; font-size: 44px; color: var(--paper); }
  .card--back .brand__mark { width: 30px; height: 30px; }
  .back-bar { position: absolute; left: 230px; top: 388px; width: 220px; height: 12px; background: var(--leaf); }

  .card--front .brand { right: 52px; top: 112px; font-size: 32px; color: var(--ink); }
  .edge-tab { position: absolute; left: 0; top: 222px; width: 12px; height: 38px; background: var(--leaf); }
  .rule { position: absolute; left: 110px; right: 50px; top: 212px; height: 2px; background: var(--leaf); }
  .person { position: absolute; left: 80px; top: 236px; }
  .person__name { font-family: "Jost", sans-serif; font-weight: 600; font-size: 28px; line-height: 34px; color: var(--ink); letter-spacing: 0.5px; }
  .person__title { font-size: 19px; line-height: 26px; color: var(--ink); }

  .contact { position: absolute; right: 46px; top: 250px; list-style: none; }
  .contact li { display: flex; justify-content: flex-end; align-items: center; gap: 14px; font-size: 19px; color: var(--ink); line-height: 34px; white-space: nowrap; }
  .contact svg { width: 16px; height: 16px; flex: none; }
  .footer-art { position: absolute; left: 0; bottom: 0; width: 700px; height: 110px; }
</style>
</head>
<body>
  <section class="card card--back" aria-label="Card back">
    <div class="brand"><span class="brand__mark"></span>ORVANTHE</div>
    <div class="back-bar"></div>
  </section>

  <section class="card card--front" aria-label="Card front">
    <div class="brand"><span class="brand__mark"></span>ORVANTHE</div>
    <div class="edge-tab"></div>
    <div class="rule"></div>
    <div class="person">
      <p class="person__name">LUKAS VARENKO</p>
      <p class="person__title">Title Fund Manager</p>
    </div>
    <ul class="contact">
      <li>+1 555 284 6190
        <svg viewBox="0 0 16 16" fill="none" stroke="#57b947" stroke-width="2"><path d="M4 2l2.5 3-1.5 2c1 2 2.5 3.5 4.5 4.5l2-1.5 3 2.5-1.5 2C7 14 2 9 2 3.5z"/></svg>
      </li>
      <li>lv@FundCorvel.com
        <svg viewBox="0 0 16 16" fill="none" stroke="#57b947" stroke-width="1.6"><rect x="1.5" y="3.5" width="13" height="9"/><path d="M1.5 3.5L8 9l6.5-5.5"/></svg>
      </li>
      <li>www.FundCorvel.com
        <svg viewBox="0 0 16 16" fill="none" stroke="#57b947" stroke-width="1.4"><circle cx="8" cy="8" r="6.5"/><ellipse cx="8" cy="8" rx="3" ry="6.5"/><path d="M1.5 8h13M2.5 5h11M2.5 11h11"/></svg>
      </li>
    </ul>
    <svg class="footer-art" viewBox="0 0 700 110" aria-hidden="true">
      <rect x="0" y="100" width="430" height="10" fill="#434f42"/>
      <polygon points="430,110 480,62 700,62 700,80 492,80 464,110" fill="#57b947"/>
      <polygon points="490,110 505,92 700,92 700,110" fill="#57b947"/>
    </svg>
  </section>
</body>
</html>
```